20 year old business card needs re-design

We need to redesign our corporate business card look. We need something that appears more modern, eye catchy but professional.

Target Market(s)

manufacturing industry

Industry/Entity Type

Manufacturer

Contact Information for Business Card

One side can have the logo. Other side can have contact information.

Font styles to use
Serif

Colors
3277b5
33b8a4
ffffff

Requirements
Must have
• Eye catchy - need to standout from the crowd. company logo cannot change. Full name, job title, phone number and email address.
Should not have
• Fax, business address is not necessary.

```html
<!DOCTYPE html>
<html lang="en">
<head>
<meta charset="utf-8">
<title>Norvale Industrial – Business Card</title>
<link href="https://fonts.googleapis.com/css2?family=Montserrat:ital,wght@0,400;0,600;0,700;0,800;1,400;1,600&display=swap" rel="stylesheet">
<style>
  :root {
    --brand-blue: #3277b5;
    --brand-teal: #33b8a4;
    --paper: #ffffff;
    --ink: #1c1c1c;
    --ink-soft: #6b6b6b;
    --rule: #8a8a8a;
    --backdrop: #e6e7e9;
    --map-tone: rgba(255,255,255,0.12);
  }
  * { box-sizing: border-box; margin: 0; padding: 0; }
  html, body { width: 1200px; height: 900px; overflow: hidden; }
  body {
    background: var(--backdrop);
    font-family: "Montserrat", sans-serif;
    position: relative;
  }
  .card {
    position: absolute;
    left: 285px;
    width: 630px;
    height: 360px;
    box-shadow: 0 6px 18px rgba(0,0,0,0.18);
    overflow: hidden;
  }
  /* Logo side */
  .card--logo { top: 55px; background: var(--brand-blue); }
  .card--logo .world-map {
    position: absolute;
    left: 40px; top: 40px; width: 550px; height: 250px;
    border-radius: 40px;
    background: radial-gradient(ellipse at center, var(--map-tone) 0%, rgba(255,255,255,0.05) 60%, transparent 75%);
  }
  .card--logo .wordmark {
    position: absolute; left: 0; right: 0; top: 135px;
    text-align: center;
    color: var(--paper);
    font-weight: 800; font-size: 46px; letter-spacing: -0.5px;
  }
  .card--logo .site {
    position: absolute; left: 0; right: 0; top: 270px;
    text-align: center; color: var(--paper);
    font-size: 15px; letter-spacing: 2px;
  }
  /* Contact side */
  .card--contact { top: 485px; background: var(--paper); }
  .card--contact .wordmark {
    position: absolute; right: 40px; top: 50px;
    color: var(--ink); font-weight: 800; font-size: 34px; letter-spacing: -0.5px;
  }
  .person { position: absolute; left: 60px; top: 168px; }
  .person__name {
    color: var(--brand-blue); font-weight: 700; font-size: 24px; letter-spacing: 0.5px;
  }
  .person__title {
    color: var(--ink-soft); font-style: italic; font-size: 14px; margin-top: 2px;
  }
  .divider {
    position: absolute; left: 60px; right: 50px; top: 238px;
    height: 2px; background: var(--rule);
  }
  .contact-list { position: absolute; left: 50px; top: 252px; list-style: none; }
  .contact-list li {
    display: flex; align-items: center; gap: 10px;
    color: var(--ink-soft); font-style: italic; font-size: 15px; line-height: 24px;
  }
  .contact-list svg { width: 14px; height: 14px; flex: none; }
  .card--contact .site {
    position: absolute; right: 50px; top: 292px;
    color: var(--ink-soft); font-size: 16px; letter-spacing: 0.5px;
  }
  .band { position: absolute; left: 0; bottom: 0; width: 630px; height: 36px; }
</style>
</head>
<body>

<section class="card card--logo">
  <div class="world-map" role="img" aria-label="Faint dotted world map spread across the card"></div>
  <div class="wordmark">Norvale Industrial</div>
  <div class="site">norvaleindustrial.com</div>
</section>

<section class="card card--contact">
  <div class="wordmark">Norvale Industrial</div>
  <div class="person">
    <div class="person__name">DANIEL REYES</div>
    <div class="person__title">Sr. Project Manager</div>
  </div>
  <div class="divider"></div>
  <ul class="contact-list">
    <li>
      <svg viewBox="0 0 14 14"><rect x="3.5" y="1" width="7" height="12" rx="1.5" fill="none" stroke="var(--brand-blue)" stroke-width="1.4"/><line x1="6" y1="11" x2="8" y2="11" stroke="var(--brand-blue)" stroke-width="1.2"/></svg>
      555-014-2700 xt 118
    </li>
    <li>
      <svg viewBox="0 0 14 14"><rect x="1" y="3" width="12" height="8" fill="var(--brand-blue)"/><polyline points="1,3 7,8 13,3" fill="none" stroke="#fff" stroke-width="1.2"/></svg>
      daniel@norvaleindustrial.com
    </li>
  </ul>
  <div class="site">NorvaleIndustrial.com</div>
  <svg class="band" viewBox="0 0 630 36" preserveAspectRatio="none">
    <polygon points="0,0 420,18 400,36 0,36" fill="var(--brand-teal)"/>
    <polygon points="428,18 630,26 630,36 408,36" fill="var(--brand-blue)"/>
  </svg>
</section>

</body>
</html>
```